New Website

New website is to be the same as Amber Lantern.

Website needs to be fully functional, with only text and logo to be added by client at a later date.

Logo has been added for reference.

```html
<!DOCTYPE html>
<html lang="en">
<head>
<meta charset="utf-8">
<title>Corvane — Avenues for Business Growth</title>
<link rel="stylesheet" href="https://fonts.googleapis.com/css2?family=Mulish:wght@300;400;600&family=Open+Sans:ital,wght@0,400;0,600;0,700;1,400;1,600&display=swap">
<style>
:root{
  --brand:#4a58b5;
  --brand-dark:#3a469c;
  --brand-light:#5c6cc9;
  --ink:#222;
  --body:#555;
  --muted:#8b8b8b;
  --white:#fff;
  --footer:#1c1c1e;
  --footer-bottom:#111113;
  --footer-text:#7e7e82;
}
*{box-sizing:border-box;margin:0;padding:0}
html,body{width:1200px;height:2571px;overflow:hidden;background:var(--white)}
body{position:relative;font-family:"Open Sans",Arial,sans-serif;color:var(--body)}
.abs{position:absolute}
.heading{font-family:"Mulish",Helvetica,sans-serif;font-weight:300;color:var(--brand);text-transform:uppercase;letter-spacing:1px}
.center{left:0;width:1200px;text-align:center}

/* header */
.site-header{top:0;left:0;width:1200px;height:108px;background:var(--white)}
.brand{left:60px;top:20px;display:flex;align-items:center;gap:14px}
.brand-mark{width:62px;height:62px;border-radius:50%;background:var(--brand)}
.brand-name{font-family:"Mulish",sans-serif;font-weight:600;font-size:34px;color:var(--brand);letter-spacing:2px}
.header-phone{right:60px;top:66px;display:flex;align-items:center;gap:12px;font-size:18px;color:var(--ink)}
.main-nav{top:108px;left:0;width:1200px;height:45px;background:linear-gradient(#5563c4,#4352ae)}
.main-nav ul{list-style:none;display:flex;padding-left:60px;height:45px;align-items:center}
.main-nav li{color:var(--white);font-size:14px;margin-right:52px}

/* hero */
.hero{top:153px;left:0;width:1200px;height:370px;background:linear-gradient(90deg,#e9eaec 0%,#d6d8dc 35%,#7d8794 55%,#3b4656 75%,#2b3442 100%)}
.hero-title{left:60px;top:222px;font-family:"Mulish",sans-serif;font-weight:300;font-size:34px;color:var(--ink);line-height:46px}
.hero-title strong{font-weight:600}
.hero-text{left:60px;top:322px;width:250px;font-size:13px;line-height:17px;color:#444}
.btn{background:linear-gradient(#5866c7,#3f4da8);color:var(--white);font-size:11px;font-weight:700;text-transform:uppercase;text-align:center;border-radius:3px;letter-spacing:.5px}
.hero-btn{left:60px;top:391px;width:110px;height:34px;line-height:34px}
.hero-dots{left:594px;top:494px;display:flex;gap:8px}
.hero-dots span{width:8px;height:8px;border-radius:50%;background:rgba(255,255,255,.5)}
.hero-dots span:first-child{background:var(--white)}
.hero-shadow{top:523px;left:170px;width:860px;height:22px;background:radial-gradient(ellipse at 50% 0,rgba(0,0,0,.35),rgba(0,0,0,0) 70%)}

/* welcome */
.welcome-title{top:562px;font-size:28px}
.welcome-text{left:70px;top:616px;width:1060px;text-align:center;font-size:13.5px;line-height:23px}
.welcome-btn{left:537px;top:687px;width:125px;height:42px;line-height:42px}

/* how it works */
.how-title{top:783px;font-size:28px}
.how-sub{top:834px;font-size:14px;font-style:italic;font-weight:600;color:var(--ink)}
.step{top:889px;width:260px;text-align:center}
.step svg{display:block;margin:0 auto}
.step h3{margin-top:22px;font-size:15px;font-weight:400;color:var(--ink);text-transform:uppercase}
.step p{margin-top:14px;font-size:13px;line-height:24px}

/* video */
.video{top:1184px;left:0;width:1200px;height:335px;background:linear-gradient(#5a5350 0%,#6d6058 35%,#3b3633 62%,#1e1c1c 100%)}
.video-title{top:1234px;font-size:28px;color:var(--white)}
.play{left:544px;top:1319px}

/* experts */
.experts-title{left:60px;top:1566px;font-size:29px}
.expert{top:1646px;width:257px}
.expert-photo{width:257px;height:169px}
.expert h3{margin-top:28px;font-family:"Mulish",sans-serif;font-weight:400;font-size:16px;color:var(--ink);text-transform:uppercase}
.expert p{margin-top:12px;font-size:13px;line-height:22px}

/* testimonials */
.testimonials{top:1980px;left:0;width:1200px;height:284px;background:linear-gradient(#5665c6,#3b48a4)}
.testimonials-title{top:2014px;font-size:28px;color:var(--white)}
.quote-mark{left:126px;top:2070px}
.quote-text{left:170px;top:2075px;width:900px;text-align:center;font-size:13.5px;line-height:23px;color:#c9cff5}
.quote-author{top:2143px;font-size:15px;font-style:italic;color:var(--white)}
.quote-dots{left:572px;top:2197px;display:flex;gap:12px}
.quote-dots span{width:11px;height:11px;border-radius:50%;background:#1f2a6d}
.quote-dots span:nth-child(2){background:#8d98e0}

/* footer */
.site-footer{top:2264px;left:0;width:1200px;height:239px;background:var(--footer)}
.footer-col{top:2312px}
.footer-col h4{font-family:"Mulish",sans-serif;font-weight:300;font-size:22px;color:var(--white);text-transform:uppercase;margin-bottom:14px}
.footer-col ul{list-style:none}
.footer-col li{font-size:13px;color:var(--footer-text);line-height:27.5px;display:flex;align-items:center;gap:10px}
.footer-col li::before{content:"";border-left:5px solid var(--footer-text);border-top:4px solid transparent;border-bottom:4px solid transparent}
.footer-col p{font-size:13px;color:var(--footer-text);line-height:23px}
.social li::before{display:none}
.social-icon{width:13px;height:13px;background:var(--footer-text);border-radius:2px}
.subscribe-input{margin-top:14px;width:257px;height:41px;background:var(--white);display:flex;align-items:center;justify-content:space-between;padding:0 14px;font-size:13px;color:var(--ink)}
.footer-bottom{top:2503px;left:0;width:1200px;height:68px;background:var(--footer-bottom);text-align:center;line-height:68px;font-size:13px;color:#4d4d52}
</style>
</head>
<body>

<header class="abs site-header">
  <div class="abs brand">
    <span class="brand-mark"></span>
    <span class="brand-name">CORVANE</span>
  </div>
  <div class="abs header-phone">
    <svg width="24" height="24" viewBox="0 0 24 24"><rect width="24" height="24" rx="4" fill="var(--brand)"/><path d="M8 6c1 0 2 2 2 3s-1 1-1 2 2 3 3 3 1-1 2-1 3 1 3 2-1 3-3 3C10 18 6 14 6 8c0-1 1-2 2-2z" fill="#fff"/></svg>
    <span>1800-555-210</span>
  </div>
</header>

<nav class="abs main-nav">
  <ul><li>Home</li><li>How it Works</li><li>Products</li><li>Blog</li><li>Help</li></ul>
</nav>

<section class="abs hero" role="img" aria-label="Photo of two smiling businessmen in suits working together at a laptop"></section>
<h1 class="abs hero-title">The Right Expert,<br><strong>Right Now</strong></h1>
<p class="abs hero-text">Neque porro quisquam est qui dolorem ipsum quia dolor sit amet, consectetur, adipisci velit...</p>
<div class="abs btn hero-btn">View Details</div>
<div class="abs hero-dots"><span></span><span></span></div>
<div class="abs hero-shadow"></div>

<h2 class="abs heading center welcome-title">Welcome to Corvane</h2>
<p class="abs welcome-text">Neque porro quisquam est, qui dolorem ipsum quia dolor sit amet, consectetur, adipisci velit, sed quia non numquam eius modi tempora incidunt ut labore et dolore magnam aliquam quaerat voluptatem. Ut enim ad minima veniam, quis nostrum exercitationem ullam corporis suscipit laboriosam</p>
<div class="abs btn welcome-btn">Read More</div>

<h2 class="abs heading center how-title">How it Works</h2>
<p class="abs center how-sub">Find an Expert who's just right for your business need. Your Expert Package includes:</p>

<div class="abs step" style="left:57px">
  <svg width="148" height="148" viewBox="0 0 148 148"><circle cx="74" cy="74" r="72" fill="none" stroke="var(--brand)" stroke-width="3"/><circle cx="74" cy="74" r="65" fill="var(--brand)"/><g fill="#fff"><rect x="70" y="38" width="14" height="38" rx="3" transform="rotate(-30 77 57)"/><rect x="50" y="96" width="48" height="7" rx="2"/><path d="M62 78a18 18 0 0 0 30 12l-5-5a11 11 0 0 1-18-7z"/></g></svg>
  <h3>Pre-Session Discovery</h3>
  <p>Nemo enim ipsam voluptatem quia voluptas sit aspernatur</p>
</div>
<div class="abs step" style="left:324px">
  <svg width="148" height="148" viewBox="0 0 148 148"><circle cx="74" cy="74" r="72" fill="none" stroke="var(--brand)" stroke-width="3"/><circle cx="74" cy="74" r="65" fill="var(--brand)"/><circle cx="74" cy="74" r="32" fill="#fff"/><g fill="none" stroke="var(--brand)" stroke-width="4"><path d="M50 60c12 4 20 14 22 40"/><path d="M60 46c18 8 36 10 44 6"/><path d="M82 70c-6 10-4 22 6 32"/></g></svg>
  <h3>One+-On-One Session</h3>
  <p>Nemo enim ipsam voluptatem quia voluptas sit aspernatur</p>
</div>
<div class="abs step" style="left:609px">
  <svg width="148" height="148" viewBox="0 0 148 148"><circle cx="74" cy="74" r="72" fill="none" stroke="var(--brand)" stroke-width="3"/><circle cx="74" cy="74" r="65" fill="var(--brand)"/><g fill="#fff"><circle cx="74" cy="56" r="10"/><path d="M58 96c0-14 7-22 16-22s16 8 16 22z"/><circle cx="50" cy="62" r="8"/><path d="M36 96c0-12 6-19 14-19 4 0 7 2 9 4-3 4-4 9-4 15z"/><circle cx="98" cy="62" r="8"/><path d="M112 96c0-12-6-19-14-19-4 0-7 2-9 4 3 4 4 9 4 15z"/></g></svg>
  <h3>Session Summary Report</h3>
  <p>Nemo enim ipsam voluptatem quia voluptas sit aspernatur</p>
</div>
<div class="abs step" style="left:885px">
  <svg width="148" height="148" viewBox="0 0 148 148"><circle cx="74" cy="74" r="72" fill="none" stroke="var(--brand)" stroke-width="3"/><circle cx="74" cy="74" r="65" fill="var(--brand)"/><g fill="none" stroke="#fff" stroke-width="8"><path d="M50 70a24 24 0 0 1 42-14"/><path d="M98 78a24 24 0 0 1-42 14"/></g><g fill="#fff"><path d="M84 46l18 2-4 18z"/><path d="M64 102l-18-2 4-18z"/></g></svg>
  <h3>Post-Session Options</h3>
  <p>Nemo enim ipsam voluptatem quia voluptas sit aspernatur</p>
</div>

<section class="abs video" role="img" aria-label="Dusky city skyline photo behind the video player"></section>
<h2 class="abs heading center video-title">Watch our Video</h2>
<svg class="abs play" width="112" height="112" viewBox="0 0 112 112"><circle cx="56" cy="56" r="50" fill="none" stroke="#fff" stroke-width="9"/><path d="M44 32l34 24-34 24z" fill="#fff"/></svg>

<h2 class="abs heading experts-title">Introducing Your Business Expert Network</h2>
<div class="abs expert" style="left:60px">
  <div class="expert-photo" role="img" aria-label="Photo of a businessman in a grey suit" style="background:linear-gradient(#5aa6d6,#8fa6b4 60%,#3c4046)"></div>
  <h3>Lorem Ipsum Dolor</h3>
  <p>Neque porro quisquam est, qui dolorem ipsum quia dolor sit amet, consectetur, adipisci velit,</p>
</div>
<div class="abs expert" style="left:334px">
  <div class="expert-photo" role="img" aria-label="Portrait photo of a smiling man in glasses" style="background:linear-gradient(#e8e8e8,#c9c2bb 60%,#4a4a4e)"></div>
  <h3>Lorem Ipsum Dolor</h3>
  <p>Neque porro quisquam est, qui dolorem ipsum quia dolor sit amet, consectetur, adipisci velit,</p>
</div>
<div class="abs expert" style="left:610px">
  <div class="expert-photo" role="img" aria-label="Photo of two colleagues reviewing documents" style="background:linear-gradient(135deg,#8d99a8,#c5c9cf 50%,#5d6470)"></div>
  <h3>Lorem Ipsum Dolor</h3>
  <p>Neque porro quisquam est, qui dolorem ipsum quia dolor sit amet, consectetur, adipisci velit,</p>
</div>
<div class="abs expert" style="left:881px">
  <div class="expert-photo" role="img" aria-label="Photo of a man and woman talking in an office" style="background:linear-gradient(135deg,#b9c3d2,#dfe3ea 50%,#6f86b7)"></div>
  <h3>Lorem Ipsum Dolor</h3>
  <p>Neque porro quisquam est, qui dolorem ipsum quia dolor sit amet, consectetur, adipisci velit,</p>
</div>

<section class="abs testimonials"></section>
<h2 class="abs heading center testimonials-title">What Clients are Saying</h2>
<svg class="abs quote-mark" width="28" height="22" viewBox="0 0 28 22"><path d="M0 12C0 5 4 1 10 0v4c-3 1-5 3-5 6h5v12H0zM16 12c0-7 4-11 10-12v4c-3 1-5 3-5 6h5v12H16z" fill="#fff"/></svg>
<p class="abs quote-text">Neque porro quisquam est, qui dolorem ipsum quia dolor sit amet, consectetur, adipisci velit, sed quia non numquam eius modi tempora incidunt ut labore et dolore magnam aliquam quaerat voluptatem.</p>
<p class="abs center quote-author">-Nora Pellham-</p>
<div class="abs quote-dots"><span></span><span></span><span></span></div>

<footer class="abs site-footer"></footer>
<div class="abs footer-col" style="left:60px">
  <h4>Quick Links</h4>
  <ul><li>About us</li><li>Our Team</li><li>Leagal</li><li>Contact us</li></ul>
</div>
<div class="abs footer-col" style="left:250px">
  <h4>Account</h4>
  <ul><li>Sign in</li><li>Register</li><li>Forget Password</li><li>Faq</li></ul>
</div>
<div class="abs footer-col" style="left:439px">
  <h4>Subscribe Newsletter</h4>
  <p style="width:250px">Do you want to get email updates from a website or blog</p>
  <div class="subscribe-input"><span>Enter Your Mail Id</span>
    <svg width="16" height="16" viewBox="0 0 16 16"><circle cx="8" cy="8" r="8" fill="#111"/><path d="M4 8h7M8 5l3 3-3 3" stroke="#fff" stroke-width="2" fill="none"/></svg>
  </div>
</div>
<div class="abs footer-col" style="left:752px">
  <h4>Contact Us</h4>
  <p style="width:230px">Nemo enim ipsam voluptatem quia voluptas sit aspernatur</p>
  <p style="margin-top:4px">1800-555-210</p>
  <p style="margin-top:4px">hello@corvane-mail.com</p>
</div>
<div class="abs footer-col social" style="left:1016px">
  <h4>Follow Us</h4>
  <ul><li><span class="social-icon"></span>Circlepage</li><li><span class="social-icon"></span>Quickpost</li><li><span class="social-icon"></span>RSS</li></ul>
</div>
<div class="abs footer-bottom">&copy; 2015 Corvane. All Right Reserved.</div>

</body>
</html>
```